Brightfield Ventures Inc. Letterhead

Creation of attractive and eye catching letterhead for a business start-up for the construction industry. Letterhead must relate to construction, but avoid standard hammer and tools in the design.

I forgot to add some details, sorry about that. Some pertinent info: Ph: 916-555-0187 brightfieldventures.example 448 Willowmere Ave, Ste 210 Folsom, CA 95999 info@brightfieldventures.example not sure if slogan should be in there" “Connecting construction professionals to create a purpose driven industry.” must be able to be used in word. Thanks!

```html
<!DOCTYPE html>
<html lang="en">
<head>
<meta charset="utf-8">
<title>Brightfield Ventures Inc. Letterhead</title>
<link href="https://fonts.googleapis.com/css2?family=Open+Sans:wght@400;600&family=Montserrat:wght@600;700&display=swap" rel="stylesheet">
<style>
  :root {
    --backdrop: #e3e3e3;
    --paper: #fbfbfb;
    --brand-red: #b70809;
    --brand-navy: #1c2a5e;
    --ink: #3a3a3a;
    --ink-strong: #444444;
    --on-red: #ffffff;
    --sig-tone: #dcdcdc;
    --watermark: rgba(28, 42, 94, 0.045);
  }
  html, body {
    margin: 0;
    padding: 0;
    width: 1200px;
    height: 945px;
    overflow: hidden;
    background: var(--backdrop);
  }
  .letterhead {
    position: absolute;
    left: 282px;
    top: 22px;
    width: 636px;
    height: 900px;
    background: var(--paper);
    box-shadow: 0 6px 18px rgba(0,0,0,0.12);
    overflow: hidden;
    font-family: "Open Sans", sans-serif;
    color: var(--ink);
  }
  .brand {
    position: absolute;
    top: 78px;
    left: 0;
    width: 100%;
    display: flex;
    justify-content: center;
    align-items: center;
    gap: 8px;
  }
  .brand-mark {
    width: 12px;
    height: 12px;
    background: var(--brand-red);
  }
  .brand-name {
    font-family: "Montserrat", sans-serif;
    font-weight: 600;
    font-size: 17px;
    letter-spacing: 1.5px;
    text-transform: uppercase;
    color: var(--brand-navy);
  }
  .watermark {
    position: absolute;
    left: 0;
    top: 440px;
    width: 100%;
    text-align: center;
    font-family: "Montserrat", sans-serif;
    font-weight: 600;
    font-size: 64px;
    line-height: 1.05;
    letter-spacing: 2px;
    text-transform: uppercase;
    color: var(--watermark);
    pointer-events: none;
  }
  .letter {
    position: absolute;
    top: 232px;
    left: 78px;
    width: 470px;
    font-size: 11.5px;
    line-height: 1.42;
  }
  .salutation {
    font-family: Arial, Helvetica, sans-serif;
    font-weight: bold;
    font-size: 13.5px;
    color: var(--ink-strong);
    margin: 0 0 10px;
  }
  .letter p.body { margin: 0 0 18px; }
  .letter p.indented { padding-left: 20px; }
  .signature {
    margin-top: 24px;
    margin-left: 20px;
    width: 150px;
    height: 48px;
    background: linear-gradient(90deg, var(--sig-tone), #ececec);
    border-radius: 4px;
  }
  .footer-band {
    position: absolute;
    left: 0;
    bottom: 0;
    width: 636px;
    height: 170px;
  }
  .contact {
    position: absolute;
    right: 22px;
    bottom: 46px;
    text-align: right;
    color: var(--on-red);
    font-style: normal;
    font-size: 10px;
    line-height: 1.7;
  }
  .contact b { font-weight: 600; }
  .contact .pin {
    display: inline-block;
    vertical-align: -1px;
    margin-right: 4px;
  }
</style>
</head>
<body>
  <main class="letterhead">
    <header class="brand">
      <span class="brand-mark"></span>
      <span class="brand-name">Brightfield Ventures Inc.</span>
    </header>

    <div class="watermark" aria-hidden="true">Brightfield<br>Ventures</div>

    <section class="letter">
      <p class="salutation">Dear Mr. Harlan,</p>
      <p class="body">Lorem Ipsum is simply dummy text of the printing and typesetting industry. Lorem Ipsum has been the industry's standard dummy text ever since the 1500s, when an unknown printer took a galley of type and scrambled it to make a type specimen book. It has survived not only five centuries, but also the leap into electronic typesetting, remaining essentially unchanged.</p>
      <p class="body indented">The standard chunk of Lorem Ipsum used since the 1500s is reproduced below for those interested. Sections 1.10.32 and 1.10.33 from "de Finibus Bonorum et Malorum" by Cicero are also reproduced in their exact original form, accompanied by English versions from the 1914 translation by H. Rackham</p>
      <p class="body indented">Lorem Ipsum is simply dummy text of the printing and typesetting industry. Lorem Ipsum has been the industry's standard dummy text ever since the 1500s, when an unknown printer took a galley of type and scrambled it to make a type specimen book. It has survived not only five centuries, but also the leap into electronic typesetting, remaining essentially unchanged. It was popularised in the</p>
      <div class="signature" role="img" aria-label="Handwritten signature of the sender"></div>
    </section>

    <svg class="footer-band" viewBox="0 0 636 170" preserveAspectRatio="none" aria-hidden="true">
      <path d="M0 95 Q330 80 636 0 L636 170 L0 170 Z" fill="var(--brand-red)"/>
      <path d="M0 88 Q330 76 636 -6" fill="none" stroke="var(--brand-navy)" stroke-width="2.2"/>
    </svg>

    <address class="contact">
      <span><svg class="pin" width="8" height="10" viewBox="0 0 8 10"><path d="M4 0a4 4 0 0 0-4 4c0 3 4 6 4 6s4-3 4-6a4 4 0 0 0-4-4z" fill="#fff"/><circle cx="4" cy="4" r="1.4" fill="#b70809"/></svg>448 Willowmere Ave, Ste 210, Folsom, CA 95999</span><br>
      <b>P.:</b> 916-555-0187 &nbsp;|&nbsp; <b>E.:</b> info@brightfieldventures.example &nbsp;|&nbsp; <b>W.:</b> www.brightfieldventures.example
    </address>
  </main>
</body>
</html>
```